Marlowe Group needs a business card

I would like the card to be simple but modern and elegant.
I like black and white.
or black and gold.
we are a private finance lender and also are involved in property and property developments.

please look at the business card photos i provided i would like M.G only one one side and all the other details on the other side use fonts that tie in with my theme.

Industry/Entity Type

Finance

Contact Information for Business Card

Marlowe Group (M.G) Daniel Marlowe M: 0413586207 E: danmarl@inboxmail.test

Font styles to use
Other font styles liked:
• Use fonts that would reflect our business

Colors
000000
ffffff

Requirements
Must have
• one side of details
• other side has either M.G or Marlowe Group like in the photos provided

```html
<!DOCTYPE html>
<html lang="en">
<head>
<meta charset="utf-8">
<title>Marlowe Group – Business Card</title>
<link href="https://fonts.googleapis.com/css2?family=Cinzel:wght@400;700&family=Lato:wght@400&display=swap" rel="stylesheet">
<style>
  :root {
    --backdrop: #808080;
    --black: #000000;
    --white: #ffffff;
    --gold: #ffcc33;
    --gold-deep: #fdc830;
    --gold-light: #ffe9a8;
    --ink: #111111;
  }
  * { margin: 0; padding: 0; box-sizing: border-box; }
  html, body { width: 1200px; height: 900px; overflow: hidden; }
  body { background: var(--backdrop); position: relative; }

  .card {
    position: absolute;
    top: 271px;
    width: 457px;
    height: 282px;
    border-radius: 12px;
    overflow: hidden;
    box-shadow: 2px 3px 6px rgba(0,0,0,0.35);
  }

  /* Details side */
  .card--details { left: 137px; background: var(--black); }
  .card__band {
    position: absolute; left: 0; width: 100%; height: 13px;
    background: linear-gradient(90deg, var(--gold-deep) 0%, var(--gold) 45%, var(--gold-light) 60%, var(--gold) 78%, var(--gold-deep) 100%);
  }
  .card__band--top { top: 0; }
  .card__band--bottom { bottom: 0; }

  .brand-mark {
    position: absolute; left: 59px; top: 84px;
    width: 145px; height: 116px;
    display: flex; align-items: center; justify-content: center; gap: 8px;
  }
  .brand-mark__square {
    width: 12px; height: 12px; border: 2px solid var(--gold); flex: none;
  }
  .brand-mark__name {
    font-family: "Cinzel", serif; font-weight: 700; font-size: 15px;
    color: var(--gold); letter-spacing: 0.5px; white-space: nowrap;
  }

  .holder {
    position: absolute; left: 232px; top: 98px;
  }
  .holder__name {
    font-family: "Cinzel", serif; font-weight: 700; font-size: 16px;
    color: var(--gold); letter-spacing: 0.3px; text-transform: uppercase;
  }
  .contact { list-style: none; margin-top: 23px; }
  .contact__item {
    display: flex; align-items: center; gap: 7px;
    font-family: "Lato", sans-serif; font-size: 13px; color: var(--white);
    line-height: 19px;
  }
  .contact__icon { width: 11px; height: 11px; flex: none; }

  /* Brand side */
  .card--brand {
    left: 627px;
    background: linear-gradient(90deg, var(--gold) 0%, var(--gold) 44%, var(--gold-light) 60%, var(--gold-light) 68%, var(--gold) 90%, var(--gold-deep) 100%);
  }
  .brand-side__square {
    position: absolute; left: 160px; top: 72px;
    width: 136px; height: 108px; border: 3px solid var(--ink);
  }
  .brand-side__name {
    position: absolute; left: 0; width: 100%; top: 189px;
    text-align: center;
    font-family: "Cinzel", serif; font-weight: 400; font-size: 19px;
    color: var(--ink); letter-spacing: 0.5px;
  }
</style>
</head>
<body>
  <section class="card card--details">
    <div class="card__band card__band--top"></div>
    <div class="brand-mark">
      <span class="brand-mark__square"></span>
      <span class="brand-mark__name">Marlowe Group</span>
    </div>
    <div class="holder">
      <h1 class="holder__name">Daniel Marlowe</h1>
      <ul class="contact">
        <li class="contact__item">
          <svg class="contact__icon" viewBox="0 0 11 11" aria-hidden="true">
            <rect x="2.5" y="0.5" width="6" height="10" rx="1" fill="none" stroke="#ffcc33" stroke-width="1.2"/>
            <rect x="4.5" y="8.3" width="2" height="1" fill="#ffcc33"/>
          </svg>
          0413586207
        </li>
        <li class="contact__item">
          <svg class="contact__icon" viewBox="0 0 11 11" aria-hidden="true">
            <rect x="0.5" y="2.5" width="10" height="7" fill="#ffcc33"/>
            <path d="M0.5 2.5 L5.5 6.5 L10.5 2.5" fill="none" stroke="#000" stroke-width="0.9"/>
          </svg>
          danmarl@inboxmail.test
        </li>
      </ul>
    </div>
    <div class="card__band card__band--bottom"></div>
  </section>

  <section class="card card--brand">
    <div class="brand-side__square"></div>
    <p class="brand-side__name">Marlowe Group</p>
  </section>
</body>
</html>
```